business card - Helicopter Flight Services, Flight School, etc.

We need a business card design for a new helicopter service.

We offer Helicopter Flight Services, Aerial Filming & Photography, Flight School, and Helicopter Tours. In that order.

Summit BladeAir, Inc.
Dennis Tollerby
SummitBladeair@Kestmail.com
626-418-7352

Based at the Brenwick Airport in Van Nuys, CA. The final design should communicate integrity and safety. Pictures or logos at your discretion.

Card back side - surprise me.

```html
<!DOCTYPE html>
<html lang="en">
<head>
<meta charset="utf-8">
<title>Summit BladeAir, Inc. – Business Card</title>
<link href="https://fonts.googleapis.com/css2?family=Arimo:wght@400&display=swap" rel="stylesheet">
<style>
  :root {
    --page-bg: #e6e6e6;
    --ink: #111111;
    --card-black: #000000;
    --navy: #1c2848;
    --white: #ffffff;
    --sky-top: #c9ccd2;
    --sky-low: #b3b5ba;
    --back-sky-top: #3f9ed9;
    --back-sky-mid: #a9d4ec;
    --back-sky-low: #8a6f8c;
    --band: rgba(255, 255, 255, 0.82);
  }
  * { margin: 0; padding: 0; box-sizing: border-box; }
  html, body {
    width: 1189px;
    height: 1200px;
    overflow: hidden;
    background: var(--page-bg);
    font-family: "Arimo", Arial, sans-serif;
  }
  .card {
    position: absolute;
    left: 140px;
    width: 918px;
    height: 522px;
    overflow: hidden;
    box-shadow: 0 4px 10px rgba(0, 0, 0, 0.25);
  }
  .card--front { top: 47px; }
  .card--back  { top: 624px; }
  .card svg { position: absolute; inset: 0; width: 100%; height: 100%; }
  .company-name {
    font-size: 52px;
    fill: var(--ink);
    letter-spacing: 1px;
  }
  .person-name {
    font-size: 37px;
    fill: var(--white);
  }
  .contact-text {
    font-size: 24px;
    fill: var(--white);
  }
  .back-title {
    font-size: 53px;
    fill: var(--ink);
    letter-spacing: 0.5px;
  }
  .back-services {
    font-size: 29px;
    fill: var(--ink);
  }
</style>
</head>
<body>

<section class="card card--front" aria-label="Business card front">
  <svg viewBox="0 0 918 522" xmlns="http://www.w3.org/2000/svg">
    <defs>
      <linearGradient id="frontSky" x1="0" y1="0" x2="0" y2="1">
        <stop offset="0" stop-color="var(--sky-top)"/>
        <stop offset="1" stop-color="var(--sky-low)"/>
      </linearGradient>
    </defs>
    <rect class="hero-photo" x="0" y="0" width="918" height="330" fill="url(#frontSky)"
          role="img" aria-label="Helicopter in flight in front of a large pale moon"/>
    <path class="accent-navy" d="M0,168 Q459,418 918,168 L918,184 Q459,444 0,184 Z" fill="var(--navy)"/>
    <path class="lower-panel" d="M0,180 Q459,440 918,180 L918,522 L0,522 Z" fill="var(--card-black)"/>
    <path class="accent-line" d="M0,168 Q459,418 918,168" fill="none" stroke="var(--white)" stroke-width="3"/>

    <text class="company-name" x="78" y="115">SUMMIT BLADEAIR, INC.</text>

    <text class="person-name" x="36" y="416">Dennis Tollerby</text>
    <line class="divider" x1="415" y1="372" x2="415" y2="500" stroke="var(--white)" stroke-width="2.5"/>

    <g class="icon icon-phone" transform="translate(462,352)">
      <rect width="17" height="17" rx="2" fill="var(--white)"/>
      <path d="M5,3.5 L7.5,3.5 L8.3,6.5 L6.8,7.6 Q8,10.2 10.2,11.3 L11.3,9.8 L14,10.6 L14,13.2 Q8,14 4.3,9 Q3.3,6.5 5,3.5 Z" fill="var(--card-black)"/>
    </g>
    <text class="contact-text" x="497" y="368">626-418-7352</text>

    <g class="icon icon-mail" transform="translate(462,397)">
      <rect width="17" height="17" rx="2" fill="var(--white)"/>
      <rect x="3" y="5" width="11" height="8" fill="var(--card-black)"/>
      <path d="M3,5 L8.5,9.5 L14,5" fill="none" stroke="var(--white)" stroke-width="1.2"/>
    </g>
    <text class="contact-text" x="497" y="412">SummitBladeair@Kestmail.com</text>

    <g class="icon icon-pin" transform="translate(462,440)">
      <rect width="17" height="17" rx="2" fill="var(--white)"/>
      <path d="M8.5,3 A4,4 0 0 1 12.5,7 Q12.5,10 8.5,14.5 Q4.5,10 4.5,7 A4,4 0 0 1 8.5,3 Z" fill="var(--card-black)"/>
      <circle cx="8.5" cy="7" r="1.5" fill="var(--white)"/>
    </g>
    <text class="contact-text" x="497" y="456">Brenwick Airport, Hangar 4B</text>
    <text class="contact-text" x="497" y="489">Van Nuys, CA</text>
  </svg>
</section>

<section class="card card--back" aria-label="Business card back">
  <svg viewBox="0 0 918 522" xmlns="http://www.w3.org/2000/svg">
    <defs>
      <linearGradient id="backSky" x1="0" y1="0" x2="0" y2="1">
        <stop offset="0" stop-color="var(--back-sky-top)"/>
        <stop offset="0.55" stop-color="var(--back-sky-mid)"/>
        <stop offset="1" stop-color="var(--back-sky-low)"/>
      </linearGradient>
    </defs>
    <rect class="back-photo" x="0" y="0" width="918" height="522" fill="url(#backSky)"
          role="img" aria-label="Helicopter overhead releasing falling roses against a blue evening sky with trees"/>
    <rect class="title-band" x="0" y="204" width="918" height="127" fill="var(--band)"/>
    <text class="back-title" x="459" y="265" text-anchor="middle">SUMMIT BLADEAIR, INC.</text>
    <text class="back-services" x="459" y="311" text-anchor="middle">Flight Services · Aerial Filming · Flight School · Tours</text>
  </svg>
</section>

</body>
</html>
```